Business Card Design for Occupational Medicine Start Up Company

We need to design a professional business card. We are a healthcare company providing occupational medicine services to blue collar industries. We are professional, efficient and high quality service providers.

Target Market(s)

Blue Collar Industry: Shipbuilding, Ports, Trucking Companies; The Executives and Safety Officers for these companies

Industry/Entity Type

Healthcare

Contact Information for Business Card

Logo, Name, Title, Email, Phone

Other font styles liked:
• Please match our Brand Guide

Requirements
Must have
• Our Company Colors and Logo

```html
<!DOCTYPE html>
<html lang="en">
<head>
<meta charset="utf-8">
<title>Crewline Health – Business Card</title>
<link href="https://fonts.googleapis.com/css2?family=Montserrat:wght@400;500;800&display=swap" rel="stylesheet">
<style>
  :root {
    --navy: #2e2a7c;
    --navy-deep: #27246b;
    --sky: #2fa3dc;
    --amber: #f4ac3a;
    --white: #ffffff;
    --ink: #2b2b33;
    --stage: #2c2c2e;
  }
  * { box-sizing: border-box; margin: 0; padding: 0; }
  html, body {
    width: 1200px; height: 1186px; overflow: hidden;
    background: var(--stage);
    font-family: "Montserrat", sans-serif;
  }
  .sheet {
    width: 1200px; height: 1186px;
    display: flex; flex-direction: column; align-items: center; justify-content: center;
    gap: 70px;
  }
  .card {
    width: 700px; height: 400px; border-radius: 26px; overflow: hidden; position: relative;
  }
  /* Front */
  .card--front {
    background: var(--navy);
    display: flex; align-items: center; justify-content: center;
  }
  .brand { display: flex; align-items: center; gap: 18px; }
  .brand__dot { width: 44px; height: 44px; border-radius: 50%; background: var(--sky); flex: none; }
  .brand__name {
    font-weight: 800; font-size: 46px; letter-spacing: 1px; text-transform: uppercase; color: var(--white);
  }
  /* Back */
  .card--back { background: var(--white); }
  .card--back .brand { position: absolute; top: 62px; left: 0; right: 0; justify-content: center; }
  .card--back .brand__name { color: var(--navy); font-size: 40px; }
  .card--back .brand__dot { width: 38px; height: 38px; }
  .top-band {
    position: absolute; top: 0; right: 0; width: 100%; height: 14px; background: var(--navy);
  }
  .details {
    position: absolute; top: 180px; left: 0; right: 0;
    display: flex; justify-content: center; align-items: center; gap: 24px;
  }
  .person { text-align: right; }
  .person__name { font-weight: 800; font-size: 27px; color: var(--navy); }
  .person__title { font-weight: 400; font-size: 16px; color: var(--ink); margin-top: 2px; }
  .divider { width: 2px; height: 78px; background: var(--navy); }
  .contact { list-style: none; display: flex; flex-direction: column; gap: 6px; }
  .contact__item { display: flex; align-items: center; gap: 10px; font-size: 16px; color: var(--ink); }
  .contact__icon { width: 16px; height: 16px; flex: none; }
  .address-band {
    position: absolute; left: 0; right: 0; bottom: 0; height: 78px; background: var(--navy);
    display: flex; align-items: center; justify-content: center;
  }
  .address { color: var(--white); font-size: 17px; font-weight: 500; letter-spacing: 0.3px; }
</style>
</head>
<body>
<main class="sheet">
  <section class="card card--front">
    <div class="brand">
      <span class="brand__dot"></span>
      <span class="brand__name">Crewline Health</span>
    </div>
  </section>

  <section class="card card--back">
    <div class="top-band"></div>
    <div class="brand">
      <span class="brand__dot"></span>
      <span class="brand__name">Crewline Health</span>
    </div>
    <div class="details">
      <div class="person">
        <p class="person__name">Daniel Reyes</p>
        <p class="person__title">CEO &amp; Founder</p>
      </div>
      <div class="divider"></div>
      <ul class="contact">
        <li class="contact__item">
          <svg class="contact__icon" viewBox="0 0 16 16"><path fill="#2fa3dc" d="M3 1l3 3-1.5 2a9 9 0 0 0 5.5 5.5L12 10l3 3-2 2C7 15 1 9 1 3z"/></svg>
          800-555-0142
        </li>
        <li class="contact__item">
          <svg class="contact__icon" viewBox="0 0 16 16"><rect x="1" y="3" width="14" height="10" rx="1" fill="#2fa3dc"/><path d="M1.5 4l6.5 5 6.5-5" fill="none" stroke="#fff" stroke-width="1.3"/></svg>
          info@crewlinehealth.com
        </li>
        <li class="contact__item">
          <svg class="contact__icon" viewBox="0 0 16 16"><circle cx="8" cy="8" r="7" fill="#2fa3dc"/><path d="M1 8h14M8 1c-3 3-3 11 0 14M8 1c3 3 3 11 0 14" fill="none" stroke="#fff" stroke-width="1"/></svg>
          www.crewlinehealth.com
        </li>
      </ul>
    </div>
    <div class="address-band">
      <p class="address">418 Harbor View Rd, #112 Lakeport, OH 43010</p>
    </div>
  </section>
</main>
</body>
</html>
```